Website for 3d printing & other services

Hi, i'm after a website to sell my 3d printed automotive parts as well as sell my 3d printing services & other services.

There's a few things i need the website to have:

- Automatic 3d print quoting based on the file the client uploads to the website.
- Shop function where i can sell my custom automotive parts
- 3D printing technologies offered are SLA & FDM
- My business can offer 3d printing, 3d scanning, 3d cad design, cnc machining, steel fabrication, drafting services.

The color design is to suit my logo which is Black, orange & white.

Target Market(s)

3d printing, automotive, fabrication

Industry/Entity Type

General manufacturing & Custom automotive parts

Coding

Coded - Design and coding required

Number of Pages Required

5+ page

Requirements
Must have
• Automatic 3d print quoting. Shop for my printed parts.

```html
<!DOCTYPE html>
<html lang="en">
<head>
<meta charset="utf-8">
<title>Korrin Draft &amp; Design</title>
<link href="https://fonts.googleapis.com/css2?family=Roboto:wght@400;500;700&display=swap" rel="stylesheet">
<style>
:root{
  --orange:#ff7300;
  --black:#000;
  --ink:#111;
  --text:#333;
  --white:#fff;
  --field:#eef3f8;
}
*{box-sizing:border-box;margin:0;padding:0}
html,body{width:1200px;height:3519px;overflow:hidden}
body{font-family:"Roboto",sans-serif;color:var(--text);background:var(--white);position:relative}
.abs{position:absolute}
.btn{display:inline-block;border-radius:20px;font-size:16px;text-align:center;line-height:38px;height:38px}
.btn-white{background:var(--white);color:var(--orange)}
.btn-orange{background:var(--orange);color:var(--white)}

/* top bar & header */
.topbar{left:315px;top:0;width:885px;height:52px;background:var(--black);clip-path:polygon(0 0,100% 0,100% 100%,35px 100%)}
.topbar p{position:absolute;left:90px;top:16px;color:var(--white);font-size:15px}
.topbar .social{position:absolute;right:105px;top:16px;display:flex;gap:16px}
.topbar .social span{width:20px;height:20px;border:2px solid var(--white);border-radius:4px}
.brand{left:110px;top:60px;width:200px;color:var(--orange);font-weight:700;font-size:28px;line-height:34px}
.contact{top:76px;font-size:13px;color:#444;line-height:22px}
.contact b{color:var(--orange);font-weight:500;font-size:16px;display:flex;align-items:center;gap:8px}
.navbar{left:0;top:164px;width:1200px;height:64px;background:var(--orange)}
.nav{left:422px;top:0;display:flex;gap:46px;line-height:64px;color:var(--white);font-size:15px}
.nav-icons{left:846px;top:18px;display:flex;gap:22px}
.navbar .btn{left:950px;top:14px;width:136px}

/* hero */
.hero{left:0;top:228px;width:1200px;height:600px;background:linear-gradient(90deg,#3b3128 0%,#6b5a4a 45%,#4a4a4e 70%,#2b2b2e 100%)}
.hero h1{left:110px;top:100px;color:var(--white);font-size:72px;line-height:84px;font-weight:700}
.hero p{left:110px;top:300px;width:540px;color:var(--white);font-size:25px;line-height:35px}
.hero .btn{left:111px;top:450px;width:137px}

/* services */
.sec-title{width:1200px;text-align:center;color:var(--ink);font-weight:700}
.sec-lead{text-align:center;font-size:15px;line-height:26px;color:#444}
.card{top:1052px;width:310px;height:413px;background:var(--white);box-shadow:0 0 6px rgba(0,0,0,.2);border-radius:4px}
.card .photo{position:absolute;left:10px;top:10px;width:290px;height:195px}
.card .label{position:absolute;left:23px;top:180px;width:264px;height:52px;background:var(--white);box-shadow:0 0 6px rgba(0,0,0,.25);color:var(--orange);font-weight:500;font-size:23px;text-align:center;line-height:52px}
.card p{position:absolute;left:20px;top:257px;width:270px;text-align:center;font-size:15px;line-height:22px;color:#333}
.card .btn{position:absolute;left:87px;top:346px;width:136px}
.arrow{top:1239px;width:44px;height:44px;border-radius:50%;background:var(--orange)}

/* automotive */
.auto{left:0;top:1553px;width:1200px;height:473px;background:var(--orange)}
.auto h2{left:112px;top:52px;color:var(--white);font-size:39px;line-height:48px;font-weight:700}
.auto p{left:112px;top:183px;width:470px;color:var(--white);font-size:15px;line-height:26px}
.auto .btn{left:112px;top:373px;width:137px}
.auto .photo{left:659px;top:18px;width:526px;height:437px;border-radius:6px;background:linear-gradient(120deg,#2e2f33,#5e6068 45%,#8a7866 70%,#4a3a30)}

/* tech */
.tab{top:2262px;width:172px;height:38px;border-radius:20px;font-size:23px;font-weight:500;text-align:center;line-height:36px}
.tab.on{left:420px;background:var(--orange);color:var(--white)}
.tab.off{left:608px;border:2px solid var(--orange);color:var(--orange)}
.tech-photo{left:110px;top:2360px;width:457px;height:411px;border-radius:4px;background:linear-gradient(135deg,#3a3f47,#1c1e22 55%,#6a3a22 80%,#25211f)}
.tech h3{left:672px;top:2385px;font-size:24px;font-weight:500;color:var(--ink)}
.tech p{left:672px;width:420px;font-size:15px;line-height:26px;color:#444}

/* quote & footer */
.footer{left:0;top:3053px;width:1200px;height:466px;background:var(--black)}
.quote-card{left:112px;top:2990px;width:977px;height:115px;background:var(--white);border-radius:10px;box-shadow:0 0 8px rgba(0,0,0,.15)}
.field{position:absolute;top:37px;width:228px;height:43px;background:var(--field);font-size:12px;color:#777;line-height:43px;padding-left:16px}
.field svg{position:absolute;right:14px;top:14px}
.quote-card .btn{position:absolute;left:783px;top:34px;width:148px;height:44px;line-height:44px;border-radius:22px;font-weight:500;font-size:17px}
.fcol{color:var(--white);font-size:15px}
.fcol h4{font-size:20px;font-weight:700;margin-bottom:28px}
.fcol li{list-style:none;line-height:30px;display:flex;align-items:center;gap:14px}
.dot{width:22px;height:22px;border-radius:50%;background:var(--orange)}
.copy{left:0;top:3466px;width:1200px;text-align:center;color:var(--white);font-size:13px}
</style>
</head>
<body>

<header>
  <div class="abs topbar">
    <p>Excepteur sint occaecat , sunt in culpa qui officia mollit anim id est laborum.</p>
    <div class="social"><span></span><span></span><span></span><span></span></div>
  </div>
  <div class="abs brand">Korrin Draft &amp; Design</div>

  <div class="abs contact" style="left:436px;width:220px">
    <b><svg width="14" height="18" viewBox="0 0 14 18"><path d="M7 0a7 7 0 0 0-7 7c0 5 7 11 7 11s7-6 7-11a7 7 0 0 0-7-7zm0 10a3 3 0 1 1 0-6 3 3 0 0 1 0 6z" fill="#ff7300"/></svg>Address</b>
    <span style="padding-left:26px;display:block">123 Korrin Lane,<br>consectetur adipiscing elit.</span>
  </div>
  <div class="abs contact" style="left:694px;top:74px">
    <b><svg width="15" height="15" viewBox="0 0 24 24"><path d="M6.6 10.8a15 15 0 0 0 6.6 6.6l2.2-2.2a1 1 0 0 1 1-.3 11 11 0 0 0 3.6.6 1 1 0 0 1 1 1V20a1 1 0 0 1-1 1A17 17 0 0 1 3 4a1 1 0 0 1 1-1h3.5a1 1 0 0 1 1 1c0 1.3.2 2.5.6 3.6a1 1 0 0 1-.3 1z" fill="#ff7300"/></svg>Phone</b>
    <span style="padding-left:24px;display:block">+1 555 010 4477</span>
  </div>
  <div class="abs contact" style="left:882px;top:74px">
    <b><svg width="16" height="12" viewBox="0 0 16 12"><rect width="16" height="12" rx="1" fill="#ff7300"/><path d="M1 1l7 5 7-5" stroke="#fff" stroke-width="1.5" fill="none"/></svg>Email</b>
    <span style="padding-left:24px;display:block">info@korrindesign.com</span>
  </div>

  <nav class="abs navbar">
    <div class="abs nav"><span>Home</span><span>About Us</span><span>Services</span><span>Contact Us</span></div>
    <div class="abs nav-icons">
      <svg width="30" height="26" viewBox="0 0 30 26" fill="none" stroke="#fff" stroke-width="2"><path d="M1 2h5l4 15h15l3-11H8"/><circle cx="12" cy="22" r="2"/><circle cx="23" cy="22" r="2"/></svg>
      <svg width="24" height="24" viewBox="0 0 24 24" fill="none" stroke="#fff" stroke-width="2"><circle cx="9" cy="9" r="7"/><path d="M14 14l8 8"/></svg>
    </div>
    <span class="abs btn btn-white">Get Started</span>
  </nav>
</header>

<section class="abs hero" role="img" aria-label="Photo of a 3D printer head printing a white lattice vase">
  <h1 class="abs">Welcome to Korrin<br>Draft &amp; Design</h1>
  <p class="abs">Lorem ipsum dolor sit amet, consectetur elit, sed do eiusmod tempor incididunt ut dolore magna aliqua.</p>
  <span class="abs btn btn-white">Get Started</span>
</section>

<section class="services">
  <h2 class="abs sec-title" style="top:908px;font-size:36px">Our Services</h2>
  <p class="abs sec-lead" style="left:200px;top:970px;width:800px">Duis aute irure dolor in reprehenderit in voluptate velit esse cillum dolore eu fugiat nulla pariatur. Excepteur sint occaecat cupidatat non proident, sunt in culpa qui officia deserunt mollit anim id est laborum."</p>

  <div class="abs arrow" style="left:49px"><svg width="44" height="44" viewBox="0 0 44 44"><path d="M25 13l-9 9 9 9" stroke="#fff" stroke-width="3" fill="none"/></svg></div>
  <div class="abs arrow" style="left:1107px"><svg width="44" height="44" viewBox="0 0 44 44"><path d="M19 13l9 9-9 9" stroke="#fff" stroke-width="3" fill="none"/></svg></div>

  <article class="abs card" style="left:112px">
    <div class="photo" role="img" aria-label="3D printer printing a white part" style="background:linear-gradient(180deg,#2a3040,#5d7fb0 60%,#cfd8e6)"></div>
    <div class="label">3d Printing</div>
    <p>Excepteur sint occaecat cupidatat non proident, sunt in culpa qui officia deserunt mollit anim id est laborum.</p>
    <span class="btn btn-orange">Read More</span>
  </article>
  <article class="abs card" style="left:446px">
    <div class="photo" role="img" aria-label="Dental 3D scanning session" style="background:linear-gradient(135deg,#e6e8ea,#9fc9cf 50%,#c9b4a4)"></div>
    <div class="label">3d Scanning</div>
    <p>Excepteur sint occaecat cupidatat non proident, sunt in culpa qui officia deserunt mollit anim id est laborum.</p>
    <span class="btn btn-orange">Read More</span>
  </article>
  <article class="abs card" style="left:780px">
    <div class="photo" role="img" aria-label="Engineer working on a CAD model on screen" style="background:linear-gradient(135deg,#4a4a3a,#7d92b4 55%,#2b4f8a)"></div>
    <div class="label">3d Cad Design</div>
    <p>Excepteur sint occaecat cupidatat non proident, sunt in culpa qui officia deserunt mollit anim id est laborum.</p>
    <span class="btn btn-orange">Read More</span>
  </article>
</section>

<section class="abs auto">
  <h2 class="abs">My Custom Automotive<br>Parts</h2>
  <p class="abs">Sed ut perspiciatis unde omnis iste natus error sit voluptatem laudantium, totam rem aperiam, eaque ipsa quae ab illo inventore veritatis et quasi architecto beatae vitae dicta sunt explicabo. Nemo enim ipsam voluptatem quia voluptas sit aspernatur aut odit aut fugit, sed quia consequuntur magni dolores eos qui ratione voluptatem sequi nesciunt.</p>
  <span class="abs btn btn-white">Shop Now</span>
  <div class="abs photo" role="img" aria-label="Two people inspecting a row of 3D printers"></div>
</section>

<section class="tech">
  <h2 class="abs sec-title" style="top:2104px;font-size:38px;font-weight:500">3D printing technologies</h2>
  <p class="abs sec-lead" style="left:250px;top:2172px;width:700px">Nemo enim ipsam voluptatem quia voluptas sit aspernatur aut odit aut fugit, sed quia consequuntur magni dolores eos qui ratione voluptatem sequi nesciunt.</p>
  <div class="abs tab on">SLA</div>
  <div class="abs tab off">FDM</div>
  <div class="abs tech-photo" role="img" aria-label="SLA resin printer build platform"></div>
  <h3 class="abs">SLA</h3>
  <p class="abs" style="top:2440px">Lorem ipsum dolor sit amet, consectetur adipiscing elit, sed do eiusmod tempor incididunt ut labore et dolore magna aliqua. Ut enim ad minim veniam, quis nostrud exercitation ullamco laboris nisi ut aliquip ex ea commodo consequat.</p>
  <p class="abs" style="top:2567px">Neque porro quisquam est, qui dolorem ipsum quia dolor sit amet, consectetur, adipisci velit, sed quia non numquam eius modi tempora incidunt ut labore et dolore magnam aliquam quaerat voluptatem.</p>
  <span class="abs btn btn-orange" style="left:672px;top:2704px;width:137px">Learn More</span>
</section>

<footer class="abs footer">
  <div class="abs fcol" style="left:113px;top:143px;width:230px">
    <h4>About Us</h4>
    <p style="line-height:21px">Duis aute irure dolor in in velit esse cillum dolore eu fugiat nulla pariatur. Excepteur sint occaecat cupidatat non proident, sunt in culpa qui officia deserunt mollit anim id est laborum.</p>
  </div>
  <div class="abs fcol" style="left:600px;top:148px">
    <h4 style="margin-bottom:14px">Quick Links</h4>
    <ul><li>Home</li><li>About Us</li><li>Services</li><li>Contact</li></ul>
  </div>
  <div class="abs fcol" style="left:980px;top:150px">
    <h4 style="margin-bottom:12px">Follow Us</h4>
    <ul>
      <li><span class="dot"></span>Chatterly</li>
      <li><span class="dot"></span>Postwave</li>
      <li><span class="dot"></span>Snapgrid</li>
      <li><span class="dot"></span>Workhall</li>
    </ul>
  </div>
  <p class="abs copy" style="top:413px">Copyright © 2023 Korrin Draft &amp; Design.All Rights Reserved.</p>
</footer>

<section class="quote">
  <h2 class="abs sec-title" style="top:2855px;font-size:50px">Get a Quote</h2>
  <p class="abs sec-lead" style="left:195px;top:2920px;width:810px;font-size:13px;line-height:22px">Lorem ipsum dolor sit amet, consectetur adipiscing elit, sed do eiusmod tempor incididunt ut labore et dolore magna aliqua. Ut enim ad minim veniam, quis nostrud exercitation ullamco laboris nisi ut aliquip ex ea commodo consequat.</p>
  <form class="abs quote-card">
    <div class="field" style="left:46px">Enter Name<svg width="14" height="14" viewBox="0 0 14 14"><circle cx="7" cy="4" r="3.5" fill="#666"/><path d="M0 14c0-4 3-6 7-6s7 2 7 6z" fill="#666"/></svg></div>
    <div class="field" style="left:291px">Enter Email<svg width="15" height="11" viewBox="0 0 16 12"><rect width="16" height="12" fill="#666"/><path d="M1 1l7 5 7-5" stroke="#fff" stroke-width="1.5" fill="none"/></svg></div>
    <div class="field" style="left:536px">Enter Phone<svg width="15" height="15" viewBox="0 0 24 24"><path d="M6.6 10.8a15 15 0 0 0 6.6 6.6l2.2-2.2a1 1 0 0 1 1-.3 11 11 0 0 0 3.6.6 1 1 0 0 1 1 1V20a1 1 0 0 1-1 1A17 17 0 0 1 3 4a1 1 0 0 1 1-1h3.5a1 1 0 0 1 1 1c0 1.3.2 2.5.6 3.6a1 1 0 0 1-.3 1z" fill="#666"/></svg></div>
    <span class="btn btn-orange">Submit</span>
  </form>
</section>

</body>
</html>
```